Kestrel Finish Studio (KFS)

I would like to design a dedicated site for my KFS product, which allows industry employees to be trained in the visual inspection of mechanical parts. My product is a 3D simulator (see https://morvint-works.ch/our-applications/virtual-reality/ and https://morvint-works.ch for videos) which makes it possible to manufacture standard parts representative of a type of defect which is accepted or refused by the quality department. These master parts can be used to create a common quality culture in the company and to train employees in a homogeneous way. The simulator is initially designed for watchmaking, but must be designed for much broader industries (cars, phone reconditioning, ball bearings, etc.)
L'information que j'ai donnée n'est pas assez précise. Je dois préciser les domaines métiers visés par le site internet. J'ai besoin de quelques jours pour choisir les domaines les plus représentatifs.
Coded - Design and coding required
1 page

```html
<!DOCTYPE html>
<html lang="en">
<head>
<meta charset="UTF-8">
<title>Kestrel Finish Studio</title>
<link href="https://fonts.googleapis.com/css2?family=Arimo:wght@400;700&family=Roboto:wght@400;500;700&display=swap" rel="stylesheet">
<style>
:root{
  --blue:#0a6dbf;
  --blue-dark:#0a4f95;
  --navy:#07183a;
  --ink:#2b2b2b;
  --text:#555;
  --white:#fff;
  --head:"Arimo",Arial,sans-serif;
  --body:"Roboto",Arial,sans-serif;
}
*{box-sizing:border-box;margin:0;padding:0}
html,body{width:1200px;height:3951px;overflow:hidden}
body{font-family:var(--body);color:var(--text);background:var(--white);position:relative}
section,header,footer{position:absolute;left:0;width:1200px;overflow:hidden}
.btn{display:inline-block;background:var(--blue);color:var(--white);font:700 15px var(--head);border-radius:24px;padding:13px 26px;text-decoration:none;letter-spacing:.2px}
h2{font:700 30px/1.6 var(--head);color:var(--ink);letter-spacing:.3px}

/* header */
.site-header{top:0;height:150px;background:var(--white)}
.brand{position:absolute;left:112px;top:14px;width:190px;text-align:center}
.brand-mark{width:74px;height:74px;border-radius:50%;background:var(--blue);margin:0 auto 12px}
.brand-name{font:700 13px/1.4 var(--head);color:var(--ink);letter-spacing:.3px}
.topbar{position:absolute;left:410px;top:0;width:790px;height:43px;background:var(--blue);clip-path:polygon(0 0,100% 0,100% 100%,45px 100%);color:var(--white);font:500 14px var(--body);display:flex;align-items:center;padding-left:64px;gap:26px}
.topbar .ic{display:inline-flex;width:30px;height:30px;border-radius:50%;background:var(--white);align-items:center;justify-content:center;margin-right:12px;vertical-align:middle}
.topbar .sep{width:1px;height:22px;background:rgba(255,255,255,.7)}
.nav{position:absolute;left:421px;top:90px;display:flex;gap:51px;font:400 15px var(--body);color:#444}
.login{position:absolute;left:967px;top:76px;padding:12px 35px}

/* hero */
.hero{top:150px;height:515px}
.hero-art{position:absolute;inset:0;background:radial-gradient(ellipse 420px 300px at 760px 250px,#8fd6ff 0%,#2a8fd8 25%,#0b3e86 60%,#061a44 100%)}
.hero-text{position:absolute;left:110px;top:133px;color:var(--white)}
.hero-text .kicker{font:400 30px var(--head);margin-bottom:14px}
.hero-text h1{font:700 46px/1.3 var(--head);letter-spacing:.5px}
.hero-text .btn{margin-top:28px;padding:12px 16px}
.arrow{position:absolute;top:236px}

/* intro */
.intro{top:665px;height:597px}
.video{position:absolute;left:134px;top:89px;width:414px;height:414px;border-radius:50%;border:7px solid var(--blue);background:radial-gradient(circle at 55% 45%,#c98a2a 0%,#5b3a10 28%,#0c0a08 60%);overflow:hidden}
.play{position:absolute;left:160px;top:160px}
.intro-copy{position:absolute;left:651px;top:88px;width:440px}
.intro-copy h2{font-size:29px;white-space:nowrap}
.intro-copy p{font:400 15px/1.78 var(--body);text-align:justify;margin:16px 0 36px}

/* control */
.control{top:1262px;height:772px;background:linear-gradient(180deg,#1478c8,#0e6ab8)}
.control h2{color:var(--white);text-align:center;margin-top:68px}
.feature{position:absolute;width:313px;height:283px;text-align:center;color:var(--white);padding:20px 14px 0}
.feature p{font:400 15px/1.78 var(--body);margin-top:14px}
.feature .more{display:inline-block;font:700 15px var(--body);margin-top:22px}
.feature.active{background:var(--white);color:#333}
.feature.active .more{color:var(--blue)}
.feature svg{display:block;margin:0 auto}

/* after-sales */
.after{top:2034px;height:591px}
.after-copy{position:absolute;left:110px;top:86px;width:480px}
.after-copy p{font:400 15px/1.78 var(--body);text-align:justify;margin:18px 0 36px}
.after-backing{position:absolute;left:646px;top:238px;width:294px;height:262px;background:var(--blue);border-radius:0 0 0 34px}
.after-photo{position:absolute;left:672px;top:87px;width:416px;height:389px;border-radius:40px;background:linear-gradient(135deg,#6d4a37,#2d2420 55%,#121418)}

/* testimonials */
.testimonials{top:2625px;height:496px;background:linear-gradient(180deg,#1577c7,#0e69b6)}
.testimonials h2{color:var(--white);text-align:center;margin-top:58px}
.t-card{position:absolute;top:153px;height:258px;border:2px solid rgba(255,255,255,.9);color:var(--white);font:400 15px/1.75 var(--body);text-align:center;padding:50px 46px}
.t-card.side{border-color:rgba(255,255,255,.45);color:rgba(255,255,255,.45);width:300px}
.quote{position:absolute;font:700 120px/1 var(--head);color:var(--white)}
.quote.dim{color:rgba(255,255,255,.4)}
.t-arrow{position:absolute;top:265px}

/* quality */
.quality{top:3121px;height:453px;background:linear-gradient(90deg,#fff 0%,#fff 55%,#eef4fb 100%);text-align:center}
.quality h2{margin-top:80px}
.quality p{width:830px;margin:42px auto 50px;font:400 15px/1.72 var(--body)}

/* footer */
.site-footer{top:3574px;height:377px;background:var(--navy);color:var(--white)}
.f-brand{position:absolute;left:108px;top:78px;width:210px;text-align:center}
.f-brand .brand-mark{width:96px;height:96px;margin-bottom:14px}
.f-brand .brand-name{color:var(--white);font-size:17px}
.f-col{position:absolute;top:80px}
.f-col h3{font:700 19px var(--head);margin-bottom:18px;letter-spacing:.3px}
.f-col li{list-style:none;font:400 15px/1.8 var(--body)}
.f-row{display:flex;gap:12px;align-items:flex-start;font:400 15px/1.6 var(--body);margin-bottom:14px}
.soc{display:flex;align-items:center;gap:14px;font:400 15px var(--body);margin-bottom:12px}
.soc i{width:32px;height:32px;border-radius:50%;border:2px solid var(--white);display:inline-block}
.email-field{width:228px;height:42px;border-radius:22px;background:var(--white);color:#999;font:400 12px var(--body);padding:14px 18px}
.submit{margin-top:10px;padding:11px 26px}
.copyright{position:absolute;top:334px;width:100%;text-align:center;font:400 15px var(--body)}
</style>
</head>
<body>

<header class="site-header">
  <div class="brand">
    <div class="brand-mark"></div>
    <div class="brand-name">KESTREL FINISH STUDIO</div>
  </div>
  <div class="topbar">
    <span><span class="ic"><svg width="14" height="11" viewBox="0 0 14 11"><rect x="0.5" y="0.5" width="13" height="10" rx="1" fill="none" stroke="#0a6dbf"/><path d="M1 1l6 5 6-5" fill="none" stroke="#0a6dbf"/></svg></span>Email:&nbsp; hello@kestrelfinish.studio</span>
    <span class="sep"></span>
    <span><span class="ic"><svg width="14" height="14" viewBox="0 0 24 24"><path d="M6.6 10.8a15 15 0 006.6 6.6l2.2-2.2a1 1 0 011-.25 11.4 11.4 0 003.6.57 1 1 0 011 1V20a1 1 0 01-1 1A17 17 0 013 4a1 1 0 011-1h3.5a1 1 0 011 1c0 1.25.2 2.45.57 3.6a1 1 0 01-.25 1z" fill="#0a6dbf"/></svg></span>Call:&nbsp; (555) 014 2290</span>
  </div>
  <nav class="nav"><span>HOME</span><span>ABOUT</span><span>SERVICES</span><span>PRODUCT</span><span>CONTACT</span></nav>
  <a class="btn login">LOG IN</a>
</header>

<section class="hero">
  <div class="hero-art" role="img" aria-label="Glowing blue digital circuit and data rings backdrop"></div>
  <div class="hero-text">
    <div class="kicker">WELCOME TO</div>
    <h1>KESTREL FINISH<br>STUDIO</h1>
    <a class="btn">GET STARTED</a>
  </div>
  <svg class="arrow" style="left:36px" width="24" height="40" viewBox="0 0 24 40"><path d="M20 4L5 20l15 16" fill="none" stroke="#1a8be0" stroke-width="6"/></svg>
  <svg class="arrow" style="left:1130px" width="24" height="40" viewBox="0 0 24 40"><path d="M4 4l15 16L4 36" fill="none" stroke="#fff" stroke-width="6"/></svg>
</section>

<section class="intro">
  <div class="video" role="img" aria-label="Video still of a polished golden ring part on black">
    <svg class="play" width="80" height="80" viewBox="0 0 80 80"><circle cx="40" cy="40" r="37" fill="none" stroke="#fff" stroke-width="4"/><path d="M31 24l24 16-24 16z" fill="none" stroke="#fff" stroke-width="4" stroke-linejoin="round"/></svg>
  </div>
  <div class="intro-copy">
    <h2>LIGHTEN THE MANAGEMENT<br>OF PHYSICAL COMPONENTS</h2>
    <p>Companies must manage and maintain sets of physical components used as a "yardstick" for the training of aesthetic testers. The cost of managing a set of physical parts representing all combinations of shapes, defect types, materials and finishes is very high. KFS allows the company to significantly reduce its management burden by scanning components or products in 3D and then virtually adding 'typical' aesthetic anomalies.</p>
    <a class="btn">LEARN MORE</a>
  </div>
</section>

<section class="control">
  <h2>HOW TO CONTROL IT?</h2>

  <div class="feature" style="left:110px;top:152px">
    <svg width="70" height="70" viewBox="0 0 70 70" fill="none" stroke="#fff" stroke-width="2.5"><circle cx="35" cy="35" r="32"/><circle cx="35" cy="35" r="25"/><rect x="12" y="30" width="46" height="12" rx="2"/><circle cx="27" cy="22" r="2.5"/><circle cx="35" cy="19" r="2.5"/><circle cx="43" cy="22" r="2.5"/></svg>
    <p>Adopting a simple and unambiguous language for a common understanding of aesthetic quality at the extended</p>
    <span class="more">Read More &rarr;</span>
  </div>
  <div class="feature active" style="left:444px;top:152px">
    <svg width="70" height="70" viewBox="0 0 70 70" fill="none" stroke="#0a6dbf" stroke-width="2.5"><rect x="25" y="3" width="20" height="12" rx="2"/><rect x="25" y="55" width="20" height="12" rx="2"/><circle cx="35" cy="35" r="21"/><circle cx="35" cy="35" r="15"/><path d="M35 25v10l6 4"/><path d="M56 31h4v8h-4"/></svg>
    <p>By using a semantic reference matrix associating the types ofanomalies (scratches, marks, deformations,</p>
    <span class="more">Read More &rarr;</span>
  </div>
  <div class="feature" style="left:776px;top:152px">
    <svg width="70" height="70" viewBox="0 0 70 70" fill="none" stroke="#fff" stroke-width="2.5"><circle cx="35" cy="17" r="10"/><path d="M25 14h20"/><path d="M14 48c2-10 10-15 21-15s19 5 21 15"/><rect x="17" y="45" width="36" height="16" rx="2"/><path d="M8 63h54"/><circle cx="35" cy="53" r="2"/></svg>
    <p>Determining the compliance thresholds of the component or product.</p>
    <span class="more">Read More &rarr;</span>
  </div>

  <div class="feature" style="left:110px;top:460px">
    <svg width="70" height="70" viewBox="0 0 70 70" fill="none" stroke="#fff" stroke-width="2.5"><circle cx="28" cy="34" r="9"/><circle cx="28" cy="34" r="3"/><circle cx="44" cy="27" r="7"/><circle cx="44" cy="27" r="2"/><path d="M4 46l14-4 12 6 14-4"/><path d="M66 20l-14 4-10-5-14 4"/><path d="M4 56l18 0 20-8 20-8"/></svg>
    <p>Providing uniform training in operational competence for those responsible for aesthetic control.</p>
    <span class="more">Read More &rarr;</span>
  </div>
  <div class="feature" style="left:444px;top:460px">
    <svg width="70" height="70" viewBox="0 0 70 70" fill="none" stroke="#fff" stroke-width="2.5"><rect x="22" y="3" width="18" height="10" rx="2"/><rect x="22" y="57" width="18" height="10" rx="2"/><circle cx="31" cy="35" r="20"/><circle cx="31" cy="35" r="13"/><path d="M31 27v8l5 3"/><circle cx="56" cy="18" r="7"/><circle cx="56" cy="18" r="2"/></svg>
    <p>By designing realistic and attractive teaching sequences for total quality control.</p>
    <span class="more">Read More &rarr;</span>
  </div>
  <div class="feature" style="left:776px;top:460px;width:333px;left:766px">
    <svg width="70" height="70" viewBox="0 0 70 70" fill="none" stroke="#fff" stroke-width="2.5"><path d="M35 8a19 19 0 00-11 34v8h22v-8A19 19 0 0035 8z"/><path d="M27 55h16M29 61h12"/><path d="M35 46V30M35 34c-6 0-8-4-8-8 5 0 8 3 8 8zM35 34c6 0 8-4 8-8-5 0-8 3-8 8z"/><path d="M8 26h5M57 26h5M14 10l4 4M56 10l-4 4"/></svg>
    <p>By regularly assessing the competence to measure the aesthetics, expressed in a tangible, reliable and sustainable way</p>
    <span class="more">Read More &rarr;</span>
  </div>
</section>

<section class="after">
  <div class="after-copy">
    <h2>IMPROVE AFTER-SALES<br>SERVICE RETURNS</h2>
    <p>The KFS platform can easily be used by the service network staff to assist them in the objective assessment of aesthetic defects by referring to the semantic matrix as well as to the cases already referenced. It is also possible, in an intuitive and playful way, to indicate, in accordance with the product nomenclature, a type of imperfection, its intensity and its location. It is also possible to draw up a precise repair estimate or to declare a non-conformity on a product coming from a market return.</p>
    <a class="btn">LEARN MORE</a>
  </div>
  <div class="after-backing"></div>
  <div class="after-photo" role="img" aria-label="Watchmaker inspecting a small movement part through a loupe with tweezers"></div>
</section>

<section class="testimonials">
  <h2>OUR TESTIMONIALS</h2>
  <div class="t-card side" style="left:-130px;text-align:right">dolor sit amet, adipiscing elit, sed do labore et dolore magna aliqua, quis nostrud ullamco nisi ex ea commodo<br><br>amet</div>
  <div class="quote dim" style="left:150px;top:280px">&rdquo;</div>
  <div class="t-card" style="left:356px;width:487px">"In the implementation of the new Qualiticien- nes en microtechnique course, the Lakeside School of Horology has deployed the KFS application to teach the methods of aesthetic control. This application fully meets the pedagogical objectives as well as the ease of use by both our teaching staff and our students."</div>
  <div class="quote" style="left:318px;top:140px">&ldquo;</div>
  <div class="quote" style="left:820px;top:282px">&rdquo;</div>
  <div class="t-card side" style="left:1013px;text-align:left">Lorem ipsum dolor sit amet, sed do eiusmod tempor magna aliqua. Ut enim exercitation ullamco<br><br>Lorem</div>
  <div class="quote dim" style="left:975px;top:140px">&ldquo;</div>
  <svg class="t-arrow" style="left:78px" width="22" height="38" viewBox="0 0 22 38"><path d="M18 3L4 19l14 16" fill="none" stroke="#fff" stroke-width="4"/></svg>
  <svg class="t-arrow" style="left:1102px" width="22" height="38" viewBox="0 0 22 38"><path d="M4 3l14 16L4 35" fill="none" stroke="#fff" stroke-width="4"/></svg>
</section>

<section class="quality">
  <h2>IMPROVING THE TOTAL QUALITY APPROACH</h2>
  <p>During the entire product life cycle, from design through customer service to distribution, the KFS application makes it possible to build up a database of aesthetic defects in a simple, efficient and computerised way. On this basis of consolidated data, it is then possible to establish recurrences, such as potential correlations, thus enabling solutions to be found to correct, improve and optimise the product, process or service offert.</p>
  <a class="btn">LEARN MORE</a>
</section>

<footer class="site-footer">
  <div class="f-brand">
    <div class="brand-mark"></div>
    <div class="brand-name">KESTREL FINISH STUDIO</div>
  </div>
  <div class="f-col" style="left:356px">
    <h3>LINKS</h3>
    <ul><li>Home</li><li>About</li><li>Services</li><li>Product</li><li>Contact</li></ul>
  </div>
  <div class="f-col" style="left:477px;width:200px">
    <h3>CONTACT US</h3>
    <div class="f-row"><svg width="16" height="20" viewBox="0 0 16 20"><path d="M8 0a7 7 0 00-7 7c0 5 7 13 7 13s7-8 7-13a7 7 0 00-7-7zm0 10a3 3 0 110-6 3 3 0 010 6z" fill="#fff"/></svg><span>Lorem ipsum dolor sit amet, consectetur</span></div>
    <div class="f-row"><svg width="16" height="16" viewBox="0 0 24 24"><path d="M6.6 10.8a15 15 0 006.6 6.6l2.2-2.2a1 1 0 011-.25 11.4 11.4 0 003.6.57 1 1 0 011 1V20a1 1 0 01-1 1A17 17 0 013 4a1 1 0 011-1h3.5a1 1 0 011 1c0 1.25.2 2.45.57 3.6a1 1 0 01-.25 1z" fill="#fff"/></svg><span>+41 00 555 12 34</span></div>
    <div class="f-row"><svg width="16" height="14" viewBox="0 0 16 12"><rect x="0.5" y="0.5" width="15" height="11" fill="none" stroke="#fff"/><path d="M1 1l7 6 7-6" fill="none" stroke="#fff"/></svg><span>info@kfs-studio.test</span></div>
  </div>
  <div class="f-col" style="left:708px">
    <h3>FOLLOW US</h3>
    <div class="soc"><i></i>Friendhub</div>
    <div class="soc"><i></i>Chirpwave</div>
    <div class="soc"><i></i>Snapframe</div>
    <div class="soc"><i></i>Worknet</div>
  </div>
  <div class="f-col" style="left:860px">
    <h3>NEWSLETTER</h3>
    <div class="email-field">Enter Email</div>
    <a class="btn submit">SUBMIT</a>
  </div>
  <div class="copyright">&copy;Copyrights 2023 KFS &nbsp;|&nbsp; All Rights Reserved</div>
</footer>

</body>
</html>
```